Unique Business Card Design

Unique Business Card design for our orthotic and prosthetic company. Our logo is on our website, color is light blue. Unique shape (artificial leg shaped, vertical, etc..) preferred. Logo, business name, individual name and basic demographics needed.

Industry/Entity Type

Business

Contact Information for Business Card

Logo, Industry, Phone # Logo, "Prosthetic & Orthotic Services" Place to add individual name and contact info

Colors
cee9f5

Requirements
Must have
• The icon must be there, placement of "Prosthetic & Orthotic Services" can be moved
Nice to have
• Like the mix of light blue, and a little darker blue. One design included the icons from my website which was a nice touch

```html
<!DOCTYPE html>
<html lang="en">
<head>
<meta charset="utf-8">
<title>Stridewell Inc. Business Card</title>
<link rel="stylesheet" href="https://fonts.googleapis.com/css2?family=Open+Sans:wght@400;600&family=Roboto:wght@400;500&display=swap">
<style>
  :root {
    --brand-blue: #0d5aa7;
    --brand-blue-light: #2a74c0;
    --brand-blue-deep: #0a4f98;
    --paper: #ffffff;
    --text-grey: #555a60;
    --rule-grey: #dcdfe3;
    --stage: #e9ebee;
  }
  * { margin: 0; padding: 0; box-sizing: border-box; }
  html, body { width: 1200px; height: 1000px; overflow: hidden; }
  body { background: var(--stage); position: relative; font-family: "Roboto", Arial, sans-serif; }

  .card {
    position: absolute;
    left: 220px;
    width: 760px;
    border-radius: 28px;
    overflow: hidden;
    box-shadow: 0 6px 18px rgba(0,0,0,0.18);
  }

  /* Front */
  .card--front {
    top: 50px;
    height: 433px;
    background: linear-gradient(120deg, var(--brand-blue-deep) 0%, var(--brand-blue) 55%, var(--brand-blue-light) 100%);
  }
  .front-mark {
    position: absolute; left: 342px; top: 197px;
    width: 140px; height: 140px; border-radius: 50%;
    background: var(--paper);
  }
  .card--front .front-mark { left: 122px; top: 147px; }
  .front-name {
    position: absolute; left: 278px; top: 166px;
    font-family: "Open Sans", Arial, sans-serif; font-weight: 600;
    font-size: 40px; letter-spacing: 0.5px; color: var(--paper);
  }
  .front-tagline {
    position: absolute; left: 300px; top: 228px;
    font-family: "Open Sans", Arial, sans-serif; font-size: 21px; color: var(--paper);
  }
  .front-web {
    position: absolute; left: 0; right: 0; top: 373px; text-align: center;
    font-family: "Open Sans", Arial, sans-serif; font-size: 16px; color: var(--paper);
    padding-left: 20px;
  }

  /* Back */
  .card--back {
    top: 524px;
    height: 436px;
    background: var(--paper);
  }
  .back-mark {
    position: absolute; left: 43px; top: 43px;
    width: 98px; height: 98px; border-radius: 50%;
    background: var(--brand-blue);
  }
  .back-name {
    position: absolute; left: 152px; top: 55px;
    font-family: "Open Sans", Arial, sans-serif; font-weight: 600;
    font-size: 28px; color: var(--brand-blue);
  }
  .back-tagline {
    position: absolute; left: 167px; top: 98px;
    font-family: "Open Sans", Arial, sans-serif; font-size: 15px; color: var(--brand-blue);
  }
  .person {
    position: absolute; right: 42px; top: 206px; text-align: right;
  }
  .person__name { font-size: 23px; font-weight: 500; color: var(--brand-blue); line-height: 28px; }
  .person__title { font-size: 16px; color: var(--text-grey); line-height: 22px; }
  .edge-tab {
    position: absolute; right: -2px; top: 211px;
    width: 12px; height: 38px; border-radius: 6px 0 0 6px;
    background: var(--brand-blue);
  }
  .divider {
    position: absolute; left: 43px; right: 42px; top: 265px;
    height: 1px; background: var(--rule-grey);
  }
  .address {
    position: absolute; left: 43px; top: 283px;
    font-size: 17px; line-height: 22px; color: var(--text-grey); letter-spacing: 0.3px;
  }
  .address__company { color: var(--brand-blue); }
  .address__web { margin-top: 8px; }
  .address__web span { color: var(--brand-blue); }
  .contacts {
    position: absolute; right: 42px; top: 282px; text-align: right;
    font-size: 17px; line-height: 24.5px; color: var(--text-grey); letter-spacing: 0.3px;
    list-style: none;
  }
  .contacts li { display: flex; justify-content: flex-end; align-items: center; gap: 7px; }
  .contacts svg { width: 12px; height: 12px; fill: var(--brand-blue); flex: none; }
  .base-rule {
    position: absolute; left: 0; right: 0; top: 413px; height: 2px; background: var(--rule-grey);
  }
  .base-band {
    position: absolute; left: 0; right: 0; top: 419px; height: 17px; background: var(--brand-blue);
  }
</style>
</head>
<body>

<section class="card card--front" aria-label="Card front">
  <div class="front-mark"></div>
  <div class="front-name">STRIDEWELL INC.</div>
  <div class="front-tagline">Prosthetic &amp; Orthotic Services</div>
  <div class="front-web">www.stridewellinc.com</div>
</section>

<section class="card card--back" aria-label="Card back">
  <div class="back-mark"></div>
  <div class="back-name">STRIDEWELL INC.</div>
  <div class="back-tagline">Prosthetic &amp; Orthotic Services</div>

  <div class="person">
    <div class="person__name">Mirela Kasprow</div>
    <div class="person__title">CO LPO</div>
  </div>
  <div class="edge-tab"></div>
  <div class="divider"></div>

  <div class="address">
    <div class="address__company">STRIDEWELL INC.</div>
    <div>2210 Harbor Lane</div>
    <div>Riverton, NY 11299</div>
    <div class="address__web">www.<span>stridewellinc</span>.net</div>
  </div>

  <ul class="contacts">
    <li>845-5550142
      <svg viewBox="0 0 12 12"><path d="M3 0h6a1 1 0 0 1 1 1v10a1 1 0 0 1-1 1H3a1 1 0 0 1-1-1V1a1 1 0 0 1 1-1zm0 1.5v7.5h6V1.5zm3 8.3a.7.7 0 1 0 0 1.4.7.7 0 0 0 0-1.4z"/></svg></li>
    <li>(718) 555-0170
      <svg viewBox="0 0 12 12"><path d="M2.5.5l2 2.4-1.2 1.4c.7 1.6 2 2.9 3.6 3.6l1.4-1.2 2.4 2-1.3 2.2C5.3 10.6 1.4 6.7.3 1.8z"/></svg></li>
    <li>(718) 555-0139
      <svg viewBox="0 0 12 12"><path d="M3 0h6v3H3zM1 4h10a1 1 0 0 1 1 1v4h-2v3H2V9H0V5a1 1 0 0 1 1-1zm2 4v3h6V8z"/></svg></li>
    <li>Mkasprow@stridewellinc.com
      <svg viewBox="0 0 12 12"><path d="M0 2h12v1L6 7 0 3zm0 2.3l6 4 6-4V10H0z"/></svg></li>
  </ul>

  <div class="base-rule"></div>
  <div class="base-band"></div>
</section>

</body>
</html>
```